Business Card Design

New business card design

Target Market(s)

Residential & Commercial Property Managers

Industry/Entity Type

Plumbing Services

Contact Information for Business Card

Name - Rowan Keddle, title - Director, Phone Number - 0431 286 517, email - rowan@tbk-plumbing.com.au, Company ABN - 73 215 904 386,

Font styles to use
Sans Serif

Colors
0054AA
0677BA
7BADD7
CADEEF
E8F1F8

```html
<!DOCTYPE html>
<html lang="en">
<head>
<meta charset="utf-8">
<title>TBK Plumbing Services – Business Card</title>
<link rel="stylesheet" href="https://fonts.googleapis.com/css2?family=Roboto:wght@300;400;700&display=swap">
<style>
  :root {
    --backdrop: #2b2c2e;
    --card-dark: #1b1c1e;
    --card-light: #f6f7f8;
    --ink: #1a1a1a;
    --muted: #8a8d92;
    --brand-deep: #0054AA;
    --brand: #0677BA;
    --brand-mid: #7BADD7;
    --brand-pale: #CADEEF;
    --brand-mist: #E8F1F8;
  }
  * { box-sizing: border-box; margin: 0; padding: 0; }
  html, body { width: 1200px; height: 852px; overflow: hidden; }
  body {
    background: var(--backdrop);
    font-family: "Roboto", sans-serif;
    position: relative;
  }
  .card {
    position: absolute;
    top: 286px;
    width: 490px;
    height: 280px;
    border-radius: 24px;
    border-bottom: 4px solid var(--brand);
    overflow: hidden;
    box-shadow: 0 14px 30px rgba(0,0,0,0.45);
  }
  .card--back { left: 80px; background: var(--card-dark); }
  .card--front { left: 630px; background: var(--card-light); }

  .wordmark {
    position: absolute;
    display: flex;
    align-items: center;
    gap: 10px;
    font-weight: 300;
    letter-spacing: 3px;
    white-space: nowrap;
  }
  .wordmark__dot {
    width: 14px; height: 14px;
    border-radius: 50%;
    background: var(--brand);
    flex: none;
  }
  .card--back .wordmark {
    left: 50%; top: 50%;
    transform: translate(-50%, -50%);
    color: #f2f2f2;
    font-size: 30px;
  }
  .card--front .wordmark {
    left: 34px; bottom: 58px;
    color: var(--ink);
    font-size: 22px;
  }

  .contact {
    position: absolute;
    left: 268px;
    top: 44px;
    color: var(--ink);
  }
  .contact__name { font-size: 20px; font-weight: 700; letter-spacing: 0.2px; }
  .contact__title { font-size: 12px; color: var(--muted); margin-top: 2px; }
  .contact__list { list-style: none; margin-top: 16px; font-size: 12.5px; line-height: 19px; color: #333; }
  .contact__list li { display: flex; align-items: center; gap: 8px; }
  .contact__list svg { width: 11px; height: 11px; fill: var(--brand); flex: none; }
  .contact__abn { margin-top: 6px; font-size: 12.5px; color: #333; }
</style>
</head>
<body>
  <section class="card card--back" aria-label="Card back">
    <div class="wordmark"><span class="wordmark__dot"></span>tbk plumbing services</div>
  </section>

  <section class="card card--front" aria-label="Card front">
    <div class="contact">
      <p class="contact__name">Rowan Keddle</p>
      <p class="contact__title">Director</p>
      <ul class="contact__list">
        <li><svg viewBox="0 0 24 24" aria-hidden="true"><path d="M6.6 10.8a15.1 15.1 0 0 0 6.6 6.6l2.2-2.2a1 1 0 0 1 1-.25 11.4 11.4 0 0 0 3.6.57 1 1 0 0 1 1 1V20a1 1 0 0 1-1 1A17 17 0 0 1 3 4a1 1 0 0 1 1-1h3.5a1 1 0 0 1 1 1c0 1.25.2 2.45.57 3.57a1 1 0 0 1-.25 1z"/></svg>0431 286 517</li>
        <li><svg viewBox="0 0 24 24" aria-hidden="true"><path d="M2 5h20v14H2z M2 5l10 8 10-8" /></svg>rowan@tbk-plumbing.com.au</li>
        <li><svg viewBox="0 0 24 24" aria-hidden="true"><circle cx="12" cy="12" r="10"/></svg>www.tbk-plumbing.com.au</li>
      </ul>
      <p class="contact__abn">ABN 73 215 904 386</p>
    </div>
    <div class="wordmark"><span class="wordmark__dot"></span>tbk plumbing services</div>
  </section>
</body>
</html>
```